Company Creation Website Redesign

Firmora88 is an Australian company creation website that specialises in creating company and trust documents. Our website was created in 2014 and we would like a new fresh look. We would like to maintain the same colour scheme of light blue and white. We feel the current landing page is a bit busy and would like something cleaner and more minimalist.

We would like all toolbar options to be the same but redesigned with better font, more aesthetically pleasing etc.

The website is built on AngularJS framework with HTML/CSS markup.

Please have a look at the current landing page.
firmora88.com.au

Target Market(s)

Accountants, those want to create company

Industry/Entity Type

Commerce

Coding

Coded - Design and coding required

Number of Pages Required

5+ page

Font styles to use
Sans Serif

Colors
0054AA
0677BA
7BADD7
CADEEF
E8F1F8

Requirements
Must have
• Attractive symbols
Nice to have
• Simple colour scheme
Should not have
• Busy images

```html
<!DOCTYPE html>
<html lang="en">
<head>
<meta charset="utf-8">
<title>Firmora88 – Australian Online Company Registration</title>
<link href="https://fonts.googleapis.com/css2?family=Poppins:ital,wght@0,400;0,500;0,600;0,700;1,400&display=swap" rel="stylesheet">
<style>
:root{
  --blue-deep:#0054AA;
  --blue:#0677BA;
  --blue-mid:#7BADD7;
  --blue-soft:#CADEEF;
  --blue-pale:#E8F1F8;
  --panel:#dde9f5;
  --ink:#1d1d1f;
  --text:#3a3a3a;
  --green:#8ab414;
  --red:#e3202f;
  --star:#f39c12;
  --footer:#1c1d21;
}
*{box-sizing:border-box;margin:0;padding:0}
html,body{width:1200px;height:5190px;overflow:hidden}
body{font-family:"Poppins",sans-serif;color:var(--text);background:#fff;position:relative}
h2.section-title{font-size:30px;font-weight:600;color:var(--ink);letter-spacing:.5px}
.btn{display:inline-flex;align-items:center;justify-content:center;color:#fff;font-weight:600;font-size:15px;letter-spacing:.5px;background:var(--blue-deep)}
.arrow{position:absolute;width:18px;height:30px}

/* header */
.site-header{position:absolute;left:0;top:0;width:1200px;height:100px;background:#fff}
.brand{position:absolute;left:75px;top:28px;display:flex;align-items:center;gap:10px;font-size:24px;font-weight:600;color:var(--blue-deep)}
.brand .mark{width:26px;height:26px;background:var(--blue-deep)}
.call{position:absolute;left:682px;top:30px;display:flex;align-items:center;gap:12px;font-size:19px;color:var(--ink)}
.call .ico{width:40px;height:40px;border-radius:50%;background:#222;display:flex;align-items:center;justify-content:center}
.call b{color:var(--blue-deep);font-weight:600}
.login{position:absolute;left:1015px;top:32px;width:112px;height:38px;font-size:15px}
.main-nav{position:absolute;left:0;top:100px;width:1200px;height:63px;background:var(--blue-deep);display:flex;align-items:center;padding-left:78px;gap:29px}
.main-nav a{color:#fff;font-size:12.5px;font-weight:600;text-decoration:none;letter-spacing:.2px}

/* hero */
.hero{position:absolute;left:0;top:163px;width:1200px;height:692px;background:linear-gradient(120deg,#6b7078 0%,#4d525a 45%,#7c8086 100%)}
.hero h1{position:absolute;top:190px;width:1200px;text-align:center;color:#fff;font-size:40px;font-weight:600}
.search{position:absolute;left:165px;top:257px;width:870px;height:62px;background:#fff;display:flex;padding:3px}
.search span{flex:1;padding-left:16px;display:flex;align-items:center;font-size:16px;color:#333}
.search .check{width:156px;height:56px;font-size:18px;font-weight:500;gap:8px}
.hero .note{position:absolute;top:338px;width:1200px;text-align:center;color:#fff;font-size:15px;font-style:italic;line-height:27px}
.promo{position:absolute;top:776px;width:512px;height:159px;text-align:center;color:#fff}
.promo h3{font-size:24px;font-weight:700;line-height:35px;margin-top:30px;letter-spacing:.5px}
.promo .btn{margin-top:30px;height:50px;padding:0 34px;font-size:16px}

/* welcome */
.welcome{position:absolute;left:0;top:1028px;width:1200px;height:540px;background:var(--panel)}
.photo{position:absolute}
.welcome .txt{position:absolute;left:617px;top:62px;width:520px}
.welcome h2{font-size:30px;font-weight:600;color:var(--ink)}
.welcome h4{font-size:20px;font-weight:600;color:var(--blue);line-height:32px;margin-top:14px}
.welcome p{font-size:14.5px;line-height:32.5px;margin-top:16px;color:var(--text)}
.welcome .btn{position:absolute;left:617px;top:412px;width:178px;height:58px}

/* services */
.service{position:absolute;top:1636px;width:242px;text-align:center}
.service .photo{position:relative;width:242px;height:168px}
.service h5{color:var(--blue);font-size:18px;font-weight:600;line-height:28px;margin-top:16px}
.service p{font-size:15px;line-height:26px;margin-top:10px}
.service strong{display:block;font-size:15px;font-weight:600;margin-top:10px;color:var(--ink)}

/* why */
.why{position:absolute;left:0;top:2082px;width:1200px;height:540px;background:var(--panel)}
.why h2{position:absolute;left:76px;top:58px;font-size:30px;font-weight:600;color:var(--ink)}
.why ul{position:absolute;left:76px;top:118px;width:520px;list-style:none}
.why li{display:flex;gap:14px;font-size:15px;line-height:26px;margin-bottom:7px}
.why li svg{flex:none;margin-top:5px}
.why .btn{position:absolute;left:76px;top:418px;width:178px;height:58px}

/* sponsors */
.sponsors{position:absolute;left:0;top:2622px;width:1200px;height:296px}
.sponsors h2{position:absolute;top:55px;width:1200px;text-align:center}
.sponsor-row{position:absolute;left:75px;top:132px;width:1050px;height:90px;display:flex;align-items:center;justify-content:space-between}
.sponsor{display:flex;align-items:center;gap:12px;font-size:26px;font-weight:600;color:var(--ink);white-space:nowrap}
.sponsor .dot{width:30px;height:30px;border-radius:50%;background:var(--ink)}

/* how */
.how{position:absolute;left:0;top:2918px;width:1200px;height:392px;background:var(--panel)}
.how h2{position:absolute;top:70px;width:1200px;text-align:center}
.step{position:absolute;top:142px;width:315px;height:172px}
.step .frame{position:absolute;inset:0;border:2px solid var(--blue);transform:skewX(-8deg)}
.step .inner{position:absolute;inset:0;display:flex;flex-direction:column;align-items:center;justify-content:center;gap:18px;color:var(--blue);font-weight:600;font-size:17px;text-align:center;line-height:26px}

/* reviews */
.reviews{position:absolute;left:0;top:3310px;width:1200px;height:390px}
.score{position:absolute;left:75px;top:62px;width:241px;height:260px;background:#eef0f2;text-align:center}
.score .rp{margin-top:26px;font-size:34px;font-weight:600;color:var(--blue)}
.score .sub{font-size:18px;color:#555;font-weight:500}
.score .sub i{color:var(--star);font-style:normal;font-size:14px}
.score .site{margin-top:22px;color:var(--blue);font-weight:600;font-size:19px}
.score .small{font-size:12.5px;font-style:italic}
.score .rating{margin-top:8px;color:var(--star);font-size:21px;font-weight:600}
.score .count{margin-top:6px;font-size:14px;font-weight:600;color:var(--ink)}
.review{position:absolute;top:62px;width:372px;height:260px;border:1px solid #dde3ea;background:#fff;padding:20px}
.review .avatar{position:absolute;left:20px;top:20px;width:72px;height:72px;border-radius:50%;background:var(--blue-soft)}
.review .name{position:absolute;left:118px;top:30px;font-size:18px;color:var(--blue);font-weight:500}
.review .stars{position:absolute;left:118px;top:58px;color:var(--star);font-size:18px;letter-spacing:3px}
.review p{position:absolute;left:20px;top:128px;right:20px;font-size:12.5px;font-style:italic;line-height:26px}

/* news */
.news{position:absolute;left:0;top:3700px;width:1200px;height:505px;background:var(--panel)}
.news h2{position:absolute;top:70px;width:1200px;text-align:center}
.post{position:absolute;top:130px;width:329px;height:215px;background:#fff;padding:22px 15px}
.post .date{color:var(--blue);font-weight:600;font-size:16px}
.post h6{font-size:16px;font-weight:600;color:var(--ink);line-height:26px;margin-top:6px}
.post p{font-size:14.5px;line-height:25px;margin-top:6px}
.news .btn{position:absolute;left:513px;top:382px;width:178px;height:56px}

/* testimonials + contact */
.bottom{position:absolute;left:0;top:4205px;width:1200px;height:530px}
.bottom h2{position:absolute;top:48px}
.quote{position:absolute;left:76px;width:480px;font-size:15px;font-style:italic;line-height:28px}
.quote b{color:var(--blue-deep);font-weight:600}
.contact-intro{position:absolute;left:615px;top:114px;width:510px;font-size:15px;line-height:28px}
.field{position:absolute;border:1px solid var(--blue-mid);background:#fff;font-size:13px;color:#333;padding:16px 18px}
.bottom .btn{position:absolute;left:615px;top:377px;width:178px;height:56px}

/* footer */
.site-footer{position:absolute;left:0;top:4735px;width:1200px;height:455px;background:var(--footer);color:#fff}
.site-footer .brand{left:75px;top:120px;color:#fff;font-size:30px}
.site-footer .brand .mark{background:#fff;width:30px;height:30px}
.copy{position:absolute;left:75px;top:200px;font-size:13px;line-height:27px}
.social{position:absolute;left:75px;top:294px;display:flex;gap:22px}
.social span{width:24px;height:24px;border-radius:50%;background:#fff}
.site-footer h6{position:absolute;top:66px;font-size:15px;font-weight:600;letter-spacing:.5px}
.links{position:absolute;left:350px;top:100px;list-style:none;font-size:14px;line-height:28.7px}
.dl-intro{position:absolute;left:705px;top:100px;width:420px;font-size:14px;line-height:28px}
.site-footer .field{border:none;left:705px;width:422px;height:56px;font-size:13px;padding:19px 18px}
.site-footer .btn{position:absolute;left:705px;top:300px;width:178px;height:58px;background:var(--blue)}
</style>
</head>
<body>

<header class="site-header">
  <div class="brand"><span class="mark"></span>Firmora88</div>
  <div class="call">
    <span class="ico"><svg width="18" height="18" viewBox="0 0 24 24"><path fill="#fff" d="M6.6 10.8a15.1 15.1 0 0 0 6.6 6.6l2.2-2.2a1 1 0 0 1 1-.25 11.4 11.4 0 0 0 3.6.57 1 1 0 0 1 1 1V20a1 1 0 0 1-1 1A17 17 0 0 1 3 4a1 1 0 0 1 1-1h3.5a1 1 0 0 1 1 1c0 1.25.2 2.45.57 3.57a1 1 0 0 1-.25 1z"/></svg></span>
    <span>Call Us: <b>03 9417 2285</b></span>
  </div>
  <a class="btn login">LOG IN</a>
</header>

<nav class="main-nav">
  <a>REGISTER COMPANY</a><a>BUSINESS NAME</a><a>SET UP TRUST</a><a>SET UP BUSINESS PLAN</a><a>REGISTER TRADE MARK</a><a>SMSF</a><a>PRICING</a><a>MORE &#9662;</a>
</nav>

<section class="hero" role="img" aria-label="Photo of a smiling man working on a laptop in an office">
  <h1>Check if company name is available</h1>
  <div class="search">
    <span>Company Name</span>
    <a class="btn check"><svg width="18" height="18" viewBox="0 0 24 24" fill="none" stroke="#fff" stroke-width="2.5"><path d="M20 12a8 8 0 1 1-2.3-5.6M20 4v5h-5"/></svg>Check</a>
  </div>
  <p class="note">We take cybercrime and credit card fraud seriously. When you purchase a service through our site,<br>we may collect your IP address for credit card security purposes.</p>
</section>

<div class="promo" style="left:75px;background:#1c4ea3">
  <h3>AUSTRALIAN ONLINE COMPANY<br>REGISTRATION</h3>
  <a class="btn" style="background:var(--green)">REGISTER NOW</a>
</div>
<div class="promo" style="left:614px;background:#1466b8">
  <h3>UPDATE YOUR COMPANY CHANGES<br>TO ASIC FOR JUST $60</h3>
  <a class="btn" style="background:var(--red)">UPDATE COMPANY DETIALS</a>
</div>

<section class="welcome">
  <div class="photo" role="img" aria-label="Photo of a hand typing on a laptop showing a registration form" style="left:0;top:0;width:588px;height:540px;background:linear-gradient(135deg,#f2f3f2,#d9dcda 60%,#c2c7c5)"></div>
  <div class="txt">
    <h2>WELCOME TO FIRMORA88</h2>
    <h4>Advanced, automated and simple company registration 24 hours a day.</h4>
    <p>We offer a fully automated, quick and cost effective company registration process. By completing an easy form, within 5 minutes you will receive full company registration documents setting up an Australian private company. We offer full customer support (telephone and email) 24 hours a day. It could not be any simpler, register your company today.</p>
  </div>
  <a class="btn">READ MORE</a>
</section>

<svg class="arrow" style="left:42px;top:1818px" viewBox="0 0 18 30"><path d="M15 2 3 15l12 13" fill="none" stroke="#333" stroke-width="2.5"/></svg>
<svg class="arrow" style="left:1140px;top:1818px" viewBox="0 0 18 30"><path d="M3 2l12 13L3 28" fill="none" stroke="#333" stroke-width="2.5"/></svg>

<div class="service" style="left:75px">
  <div class="photo" role="img" aria-label="Photo of a hand using a tablet" style="background:linear-gradient(135deg,#cdd6e0,#8d9aa8)"></div>
  <h5>Quick, simple and seamless company registration</h5>
  <p>Completed in 3 easy steps for $44 (exc GST).<br>Plus $512 ASIC registration fee.</p>
  <strong>As simple as 1, 2, 3.</strong>
</div>
<div class="service" style="left:345px">
  <div class="photo" role="img" aria-label="Photo of people signing documents on a desk" style="background:linear-gradient(135deg,#d8d6d0,#8f8b84)"></div>
  <h5>Quick, Simple Discretionary and Unit Trust Registration</h5>
  <p>Completed in 3 easy steps for $129 (exc GST).</p>
  <strong>As simple as 1, 2, 3.</strong>
</div>
<div class="service" style="left:615px">
  <div class="photo" role="img" aria-label="Photo of a trademark stamp on paper" style="background:linear-gradient(135deg,#e4e6e8,#9aa0a6)"></div>
  <h5>Quick, Simple Trademark application</h5>
  <p>Completed in 3 easy steps from $180 (exc GST).</p>
  <strong>As simple as 1, 2, 3.</strong>
</div>
<div class="service" style="left:885px">
  <div class="photo" role="img" aria-label="Photo of a trademark application form on a computer screen" style="background:linear-gradient(135deg,#dfe4ea,#8e99a5)"></div>
  <h5>Quick, Simple International Trademark application</h5>
  <p>Completed in 3 easy steps.</p>
  <strong>As simple as 1, 2, 3.</strong>
</div>

<section class="why">
  <h2>WHY USE US</h2>
  <ul>
    <li><svg width="16" height="16" viewBox="0 0 16 16"><circle cx="8" cy="8" r="6.8" fill="none" stroke="#0677BA" stroke-width="1.6"/><path d="M5 8.2l2 2 4-4" fill="none" stroke="#0677BA" stroke-width="1.6"/></svg>Quick and simple registration process.</li>
    <li><svg width="16" height="16" viewBox="0 0 16 16"><circle cx="8" cy="8" r="6.8" fill="none" stroke="#0677BA" stroke-width="1.6"/><path d="M5 8.2l2 2 4-4" fill="none" stroke="#0677BA" stroke-width="1.6"/></svg>Company registered in less than 5 minutes.</li>
    <li><svg width="16" height="16" viewBox="0 0 16 16"><circle cx="8" cy="8" r="6.8" fill="none" stroke="#0677BA" stroke-width="1.6"/><path d="M5 8.2l2 2 4-4" fill="none" stroke="#0677BA" stroke-width="1.6"/></svg>Full documentation emailed to you so you can start trading.</li>
    <li><svg width="16" height="16" viewBox="0 0 16 16"><circle cx="8" cy="8" r="6.8" fill="none" stroke="#0677BA" stroke-width="1.6"/><path d="M5 8.2l2 2 4-4" fill="none" stroke="#0677BA" stroke-width="1.6"/></svg>ASIC agent 58203.</li>
    <li><svg width="16" height="16" viewBox="0 0 16 16"><circle cx="8" cy="8" r="6.8" fill="none" stroke="#0677BA" stroke-width="1.6"/><path d="M5 8.2l2 2 4-4" fill="none" stroke="#0677BA" stroke-width="1.6"/></svg>Prepared by a qualified lawyer and accountant.</li>
    <li><svg width="16" height="16" viewBox="0 0 16 16"><circle cx="8" cy="8" r="6.8" fill="none" stroke="#0677BA" stroke-width="1.6"/><path d="M5 8.2l2 2 4-4" fill="none" stroke="#0677BA" stroke-width="1.6"/></svg>Full telephone and email customer support available 24 hours a day.</li>
    <li><svg width="16" height="16" viewBox="0 0 16 16"><circle cx="8" cy="8" r="6.8" fill="none" stroke="#0677BA" stroke-width="1.6"/><path d="M5 8.2l2 2 4-4" fill="none" stroke="#0677BA" stroke-width="1.6"/></svg>The simplest and most cost effective company registration process available.</li>
  </ul>
  <a class="btn">READ MORE</a>
  <div class="photo" role="img" aria-label="Photo of a smiling woman working at a desk with a laptop" style="left:612px;top:0;width:588px;height:540px;background:linear-gradient(135deg,#e8e6e2,#c9c4bc 55%,#8a7a68)"></div>
</section>

<section class="sponsors">
  <h2 class="section-title">LIST OF SPONSORS</h2>
  <div class="sponsor-row">
    <div class="sponsor"><span class="dot"></span>Swiftlink Traffic</div>
    <div class="sponsor">Harbourstay</div>
    <div class="sponsor"><span class="dot"></span>Norwood Finance</div>
    <div class="sponsor">Tilepay</div>
  </div>
</section>

<section class="how">
  <h2 class="section-title">HOW IT WORKS</h2>
  <div class="step" style="left:85px"><div class="frame"></div><div class="inner">
    <svg width="44" height="54" viewBox="0 0 44 54" fill="none" stroke="#0677BA" stroke-width="4"><path d="M4 4h24l12 12v34H4z"/><path d="M12 26h20M12 34h20M12 42h14"/></svg>
    Fill in a short form</div></div>
  <div class="step" style="left:446px"><div class="frame"></div><div class="inner">
    <svg width="56" height="56" viewBox="0 0 56 56" fill="none" stroke="#0677BA" stroke-width="4"><circle cx="28" cy="28" r="24"/><path d="M28 14v15l9 6"/></svg>
    Company registered in less<br>than 5 minutes</div></div>
  <div class="step" style="left:802px"><div class="frame"></div><div class="inner">
    <svg width="58" height="50" viewBox="0 0 58 50" fill="#0677BA"><rect x="0" y="0" width="4" height="50"/><rect x="0" y="46" width="58" height="4"/><rect x="12" y="24" width="6" height="18"/><rect x="24" y="10" width="6" height="32"/><rect x="36" y="18" width="6" height="24"/><rect x="48" y="6" width="6" height="36"/></svg>
    Start trading<br>using your company</div></div>
</section>

<section class="reviews">
  <div class="score">
    <div class="rp">ReviewPoint</div>
    <div class="sub">Reviews <i>★★★★★</i></div>
    <div class="site">firmora88.com.au</div>
    <div class="small">Online Company Registration</div>
    <div class="rating">★★★★★ 4.8</div>
    <div class="count">Based on 220 reviews</div>
  </div>
  <svg class="arrow" style="left:334px;top:180px" viewBox="0 0 18 30"><path d="M15 2 3 15l12 13" fill="none" stroke="#333" stroke-width="2.5"/></svg>
  <div class="review" style="left:366px">
    <span class="avatar"></span><span class="name">Daniel Moreno</span><span class="stars">★★★★★</span>
    <p>This company provides their customers a professional responsive experience, they provide a high quality service at a great value. Would not go anywhere else as you would be hard pressed to get this level of expertise without the price tag.</p>
  </div>
  <div class="review" style="left:756px">
    <span class="avatar"></span><span class="name">Daniel Moreno</span><span class="stars">★★★★★</span>
    <p>This company provides their customers a professional responsive experience, they provide a high quality service at a great value. Would not go anywhere else as you would be hard pressed to get this level of expertise without the price tag.</p>
  </div>
  <svg class="arrow" style="left:1140px;top:180px" viewBox="0 0 18 30"><path d="M3 2l12 13L3 28" fill="none" stroke="#333" stroke-width="2.5"/></svg>
</section>

<section class="news">
  <h2 class="section-title">LATEST NEWS</h2>
  <svg class="arrow" style="left:42px;top:222px" viewBox="0 0 18 30"><path d="M15 2 3 15l12 13" fill="none" stroke="#333" stroke-width="2.5"/></svg>
  <article class="post" style="left:75px"><div class="date">MAR07, 2022</div><h6>BE AWARE OF TRADEMARK SCAM AND FALSE BILLING</h6><p>In this year, we often see an increase reports of false billing and unsolicited invoices being sent to our trademark applicants.</p></article>
  <article class="post" style="left:437px"><div class="date">MAR07, 2022</div><h6>BE AWARE OF TRADEMARK SCAM AND FALSE BILLING</h6><p>In this year, we often see an increase reports of false billing and unsolicited invoices being sent to our trademark applicants.</p></article>
  <article class="post" style="left:799px"><div class="date">MAR07, 2022</div><h6>BE AWARE OF TRADEMARK SCAM AND FALSE BILLING</h6><p>In this year, we often see an increase reports of false billing and unsolicited invoices being sent to our trademark applicants.</p></article>
  <svg class="arrow" style="left:1140px;top:222px" viewBox="0 0 18 30"><path d="M3 2l12 13L3 28" fill="none" stroke="#333" stroke-width="2.5"/></svg>
  <a class="btn">READ ALL NEWS</a>
</section>

<section class="bottom">
  <h2 class="section-title" style="left:76px">TESTIMONIALS</h2>
  <p class="quote" style="top:110px">“ In this year, we often see an increase reports of false billing and unsolicited invoices being sent to our trademark applicants...”<b>Peter Hale</b></p>
  <p class="quote" style="top:220px">“ In this year, we often see an increase reports of false billing and unsolicited invoices being sent to our trademark applicants...”<b>Peter Hale</b></p>
  <p class="quote" style="top:330px">“ In this year, we often see an increase reports of false billing and unsolicited invoices being sent to our trademark applicants...”<b>Peter Hale</b></p>
  <h2 class="section-title" style="left:615px">QUICK CONTACT</h2>
  <p class="contact-intro">Simply complete a short form and one of our experienced support staff will contact you.</p>
  <div class="field" style="left:615px;top:193px;width:249px;height:53px">Name</div>
  <div class="field" style="left:875px;top:193px;width:250px;height:53px">Email Address</div>
  <div class="field" style="left:615px;top:256px;width:510px;height:108px">Message</div>
  <a class="btn">SUBMIT</a>
</section>

<footer class="site-footer">
  <div class="brand"><span class="mark"></span>Firmora88</div>
  <p class="copy">2022 © Firmora88 Pty Ltd<br>All Right Reserved</p>
  <div class="social"><span></span><span></span><span></span><span></span><span></span></div>
  <h6 style="left:350px">QUICK LINKS</h6>
  <ul class="links">
    <li>Register Company</li><li>Business Name</li><li>Set Up Trust</li><li>Set Up Business Plan</li><li>Register Trade Mark</li><li>Smsf</li><li>Property Withholding Clearance Certificate</li><li>Abn Registration</li><li>Legal &amp; Tax Consultations</li><li>Pricing</li><li>Resources</li>
  </ul>
  <h6 style="left:705px">DOWNLOAD DOCUMENTS</h6>
  <p class="dl-intro">Log in with your User ID and Password to download your company documents.</p>
  <div class="field" style="top:170px">Enter Name</div>
  <div class="field" style="top:235px">Enter Email Address</div>
  <a class="btn">SUBMIT</a>
</footer>

</body>
</html>
```